Create a book cover for lesbian erotic romance retelling of Liora Frost "The Maiden and the Thorned...

I need a book cover for a lesbian erotic romance retelling of Liora Frost. The cover should high-light both the erotic and the romantic mood, and it should't be too dark. It should also capture the feeling of an old fairytale (think more classic Korvath Brothers, less Velmont). The classic symbols apply: red apple, mirror, etc., but they're not neccesary for the design. The book takes place in a fairytale-like medieval time, so no modern-day designs, please.The details of the book are as follows:
- Title: The Maiden and the Thorned Regent
- Author: Nessa Hartwell
- Text for the the back cover (there may be some changes to this, but it will give you an idea of the feel of the book):"Once upon a time, there was a princess named Liora Frost, and a fierce Thorned Regent.Fated by powers of old to be enemies, The Maiden and the Thorned Regent doom the world to a never-ending war. However, under a dark and rainy sky, the Thorned Regent proposes a deal to end the war of all wars: Liora Frost will spend a lunar cycle under the Thorned Regent's services, and on the last day she will make a choice to leave or stay. If the princess chooses to leave, then the queen will abandon her palace and vanish, never to be heard of again; but if she chooses to stay, then the war will end, and balance will be restored.Liora Frost accepts the queen’s deal, hardly guessing that the services she’s expected to provide include the queen’s bed and her pleasure. As The Maiden and the Thorned Regent tangle themselves between the sheets, secrets are uncovered, old feelings resurface, and lust soon becomes something more. But the Thorned Regent has a secret plan, and love might not be enough to stop her on time.Can Liora Frost put behind the Thorned Regent’s attempts on her life, and convince her that there’s a future where they stand together and in love? Can the Thorned Regent forget her destiny of avenging fury, and allow herself the selfish pleasure of love?The Thorned Regent is a lesbian erotic romance retelling of the classic fairytale Liora Frost, where destiny twists itself with desire and love, where not everything is what it seems, and where hopefully, love will conquer all.

If you're going to go with female figures, it's important that "Liora Frost" looks properly pale-faced, dark-haired and red-lipped. The "Thorned Regent" has dark copper hair and skin a little darker, if you're going for that kind of detail.I'm really open to suggestions.
It just needs to be sexy, feminine and subtle.

Target Market(s)

18+ LGBT females, erotica lovers, fairytale lovers

Font styles to use
Serif
Sans Serif
Decorative
Script

Colors

Requirements
Must have
• I'm open to suggestions.
Nice to have
Should not have
• Tacky, overly suggestive images.

```html
<!DOCTYPE html>
<html lang="en">
<head>
<meta charset="utf-8">
<title>The Maiden and the Thorned Regent — Cover Wrap</title>
<link href="https://fonts.googleapis.com/css2?family=Kaushan+Script&family=Cinzel:wght@400;600&display=swap" rel="stylesheet">
<style>
  :root {
    --stage: #d9dadc;
    --cover-ink: #170d13;
    --title-white: #f7f5f4;
    --body-white: #efeae8;
    --spine-peach: #e9a877;
    --spine-ink: #1c1115;
    --photo-dark: #1e1417;
    --photo-skin: #b9796a;
    --photo-hair: #6b4a32;
    --photo-dress: #8fa3c4;
  }
  * { box-sizing: border-box; margin: 0; padding: 0; }
  html, body {
    width: 1200px; height: 850px; overflow: hidden;
    background: var(--stage);
  }
  .wrap {
    position: absolute; left: 115px; top: 75px;
    display: flex; height: 700px;
    box-shadow: 0 12px 30px rgba(0,0,0,.25);
  }
  .back-cover, .front-cover {
    position: relative; width: 460px; height: 700px;
    background: var(--cover-ink); overflow: hidden;
  }
  .spine {
    position: relative; width: 50px; height: 700px;
    background: var(--spine-peach);
    display: flex; align-items: center; justify-content: center;
    overflow: hidden;
  }
  .spine-line {
    transform: rotate(-90deg); white-space: nowrap;
    display: flex; align-items: center; gap: 34px;
    color: var(--spine-ink);
  }
  .spine-author {
    font-family: "Cinzel", serif; font-size: 15px; letter-spacing: 5px;
  }
  .spine-title {
    font-family: "Kaushan Script", cursive; font-size: 24px;
  }
  .title {
    font-family: "Kaushan Script", cursive; color: var(--title-white);
    font-weight: 400; line-height: .95; position: relative;
  }
  .title-line { display: block; }
  .title-small { font-size: .42em; display: inline-block; vertical-align: top; margin-top: .2em; }
  .front-title { position: absolute; left: 22px; top: 40px; font-size: 78px; }
  .front-title .line-two { margin-left: 14px; }
  .front-title .line-three { margin-left: 150px; }
  .back-title { text-align: center; font-size: 46px; padding-top: 48px; }
  .photo {
    position: absolute; left: 0; right: 0; bottom: 0; height: 420px;
    background:
      radial-gradient(ellipse at 30% 55%, var(--photo-skin) 0%, transparent 38%),
      radial-gradient(ellipse at 72% 70%, var(--photo-skin) 0%, transparent 35%),
      radial-gradient(ellipse at 20% 20%, var(--photo-dress) 0%, transparent 30%),
      radial-gradient(ellipse at 50% 50%, var(--photo-hair) 0%, transparent 60%),
      var(--photo-dark);
  }
  .photo-fade {
    position: absolute; left: 0; right: 0; bottom: 340px; height: 120px;
    background: linear-gradient(to bottom, var(--cover-ink) 20%, rgba(23,13,19,0));
  }
  .front-author {
    position: absolute; left: 26px; right: 26px; bottom: 30px;
    font-family: "Cinzel", serif; font-size: 28px; letter-spacing: 6px;
    color: var(--title-white); white-space: nowrap; text-align: center;
  }
  .blurb {
    font-family: "Cinzel", serif; text-transform: uppercase;
    color: var(--body-white); font-size: 10.6px; line-height: 1.62;
    letter-spacing: .2px; padding: 28px 38px 0; text-align: justify;
  }
</style>
</head>
<body>
  <main class="wrap">
    <section class="back-cover">
      <h2 class="title back-title">
        <span class="title-line">The Maiden</span>
        <span class="title-line">Thorned <span class="title-small">and the</span> Regent</span>
      </h2>
      <p class="blurb">Once upon a time, there was a princess named Liora Frost, and a fierce Thorned Regent. Fated by powers of old to be enemies, The Maiden and the Thorned Regent doom the world to a never-ending war. However, under a dark and rainy sky, the Thorned Regent proposes a deal to end the war of all wars: Liora Frost will spend a lunar cycle under the Thorned Regent's services, and on the last day she will make a choice to leave or stay. If the princess chooses to leave, then the regent will abandon her palace and vanish, never to be heard of again; but if she chooses to stay, then the war will end, and balance will be restored. Liora Frost accepts the regent's deal, hardly guessing that the services she's expected to provide include the regent's bed and her pleasure. As The Maiden and the Thorned Regent tangle themselves between the sheets, secrets are uncovered, old feelings resurface, and lust soon becomes something more. But the Thorned Regent has a secret plan, and love might not be enough to stop her on time. Can Liora Frost put behind the Thorned Regent's attempts on her life, and convince her that there's a future where they stand together and in love? Can the Thorned Regent forget her destiny of avenging fury, and allow herself the selfish pleasure of love? The Thorned Regent is a lesbian erotic romance retelling of a classic fairytale, where destiny twists itself with desire and love, where not everything is what it seems, and where hopefully, love will conquer all.</p>
    </section>

    <aside class="spine">
      <div class="spine-line">
        <span class="spine-author">NESSA HARTWELL</span>
        <span class="spine-title">The Maiden and the Thorned Regent</span>
      </div>
    </aside>

    <section class="front-cover">
      <div class="photo" role="img" aria-label="Photograph of two smiling women lying head to head among wildflowers, covering each other's eyes and faces with their hands"></div>
      <div class="photo-fade"></div>
      <h1 class="title front-title">
        <span class="title-line">The Maiden</span>
        <span class="title-line line-two">Thorned <span class="title-small">and the</span></span>
        <span class="title-line line-three">Regent</span>
      </h1>
      <p class="front-author">NESSA HARTWELL</p>
    </section>
  </main>
</body>
</html>
```